Norvane Hand Wash

Design hand washes. Total 12 variants to be designed.

Variants name are:

1) MILK &OLIVE
2) Shea Butter
3) Velvet Bloom
4) Cream and Peach
5) Milk and Honey
6) Vanilla Mystery
7) Bakhour
8) Musk
9) White Oud
10) Black Oud
11) Rose Oud
12) Oud & Sandalwood

Labels can be on transparent sticker or background colors. All variants will be differentiated by fragrances and color. Bottle will be transparent. Pumps used for dispensing will be in Black or Transparent Color.

Designers can initially present designs of 4-5 variants initially. Later based on feedback, they can work out on more.

Bottle is 400ml and shape is rectangle. Ignore the size on bottle picture. Bottle keyline is attached.

Target Market(s)

B+, B, C+

Requirements
Must have
• Some relation to the variant names

```html
<!DOCTYPE html>
<html lang="en">
<head>
<meta charset="utf-8">
<title>Norvane Hand Wash Range</title>
<link rel="stylesheet" href="https://fonts.googleapis.com/css2?family=Lato:wght@400;700&family=Dancing+Script:wght@700&display=swap">
<style>
:root{
  --page:#ffffff;
  --pump-light:#f4f4f4;
  --pump-mid:#d9d9d9;
  --pump-dark:#b9b9b9;
  --label-light:#fffdfb;
  --brand:#5a4a9c;
  --small-text:#4a4a4a;
  --box-text:#ffffff;
}
*{margin:0;padding:0;box-sizing:border-box}
html,body{width:770px;height:1200px;overflow:hidden;background:var(--page)}
.range{position:relative;width:770px;height:1200px}
.bottle{position:absolute;width:136px;height:320px}
.pump-nozzle{position:absolute;left:30px;top:0;width:106px;height:12px;border-radius:3px 6px 2px 2px;background:linear-gradient(180deg,var(--pump-light),var(--pump-dark))}
.pump-stem{position:absolute;left:58px;top:12px;width:28px;height:22px;background:linear-gradient(90deg,var(--pump-dark),var(--pump-light) 45%,var(--pump-mid))}
.pump-collar{position:absolute;left:38px;top:32px;width:63px;height:58px;border-radius:4px 4px 0 0;background:linear-gradient(90deg,var(--pump-dark),var(--pump-light) 40%,var(--pump-mid) 80%,var(--pump-dark))}
.body{position:absolute;left:0;top:88px;width:136px;height:232px;border-radius:16px;background:linear-gradient(90deg,color-mix(in srgb,var(--tint) 85%,#000) 0%,var(--tint) 12%,color-mix(in srgb,var(--tint) 80%,#fff) 50%,var(--tint) 88%,color-mix(in srgb,var(--tint) 85%,#000) 100%);box-shadow:0 8px 10px -6px rgba(0,0,0,.12)}
.label{position:absolute;left:18px;top:16px;width:100px;height:194px;border-radius:8px;background:radial-gradient(circle at 50% 40%,var(--label-light) 30%,color-mix(in srgb,var(--tint) 35%,#fff) 100%);text-align:center;overflow:hidden}
.brand{position:absolute;left:0;right:0;top:28px;font:700 17px/1 "Lato",sans-serif;color:var(--brand)}
.variant-line{position:absolute;left:0;right:0;top:70px;font:400 11px/1 "Lato",sans-serif;color:var(--small-text)}
.variant-line.accent{color:var(--ink)}
.variant-name{position:absolute;left:0;right:0;top:81px;font:700 27px/1 "Dancing Script",cursive;color:var(--ink);white-space:nowrap}
.variant-name.long{font-size:19px;top:86px}
.art{position:absolute;left:24px;top:113px;width:52px;height:42px;border-radius:50%;background:radial-gradient(circle at 40% 35%,color-mix(in srgb,var(--art) 55%,#fff),var(--art))}
.size-box{position:absolute;left:33px;top:157px;width:34px;height:37px;background:var(--box);color:var(--box-text);font-family:"Lato",sans-serif;padding-top:5px}
.size-box .kind{display:block;font-size:5.5px;font-weight:700;letter-spacing:1.2px;line-height:1.2}
.size-box .volume{display:block;margin-top:6px;font-size:4.5px;line-height:1}
.olive{--tint:#cadb84;--ink:#4e7a1d;--box:#3d5a1e;--art:#8fb02e;left:74px;top:62px}
.peach{--tint:#f8b084;--ink:#a3212a;--box:#8a2b22;--art:#f59a3c;left:237px;top:62px}
.vanilla{--tint:#f2ead9;--ink:#8a5a2b;--box:#6d4a2e;--art:#7a4a25;left:398px;top:62px}
.rose{--tint:#dd8ba4;--ink:#c81e4e;--box:#c41c57;--art:#e79aa4;left:562px;top:62px}
.sandalwood{--tint:#f59a2e;--ink:#4a2c1a;--box:#5a4430;--art:#7b4a2e;left:74px;top:438px}
.musk{--tint:#fcd373;--ink:#e0573d;--box:#e86a48;--art:#f3e37a;left:237px;top:438px}
.honey{--tint:#d9822f;--ink:#d86a1b;--box:#e0842a;--art:#e9a125;left:398px;top:438px}
.shea{--tint:#efe6c3;--ink:#3e3a2e;--box:#555342;--art:#7a5a35;left:562px;top:438px}
.bloom{--tint:#c62d45;--ink:#a1182d;--box:#b41c36;--art:#d85a3a;left:74px;top:812px}
</style>
</head>
<body>
<main class="range">

<article class="bottle olive">
  <div class="pump-nozzle"></div><div class="pump-stem"></div><div class="pump-collar"></div>
  <div class="body"><div class="label">
    <div class="brand">Norvane</div>
    <div class="variant-line">Milk and</div>
    <div class="variant-name">Olive</div>
    <div class="art" role="img" aria-label="Green olives with leaves"></div>
    <div class="size-box"><span class="kind">HAND WASH</span><span class="volume">- 400 mL -</span></div>
  </div></div>
</article>

<article class="bottle peach">
  <div class="pump-nozzle"></div><div class="pump-stem"></div><div class="pump-collar"></div>
  <div class="body"><div class="label">
    <div class="brand">Norvane</div>
    <div class="variant-line">Cream and</div>
    <div class="variant-name">Peach</div>
    <div class="art" role="img" aria-label="Ripe peaches"></div>
    <div class="size-box"><span class="kind">HAND WASH</span><span class="volume">- 400 mL -</span></div>
  </div></div>
</article>

<article class="bottle vanilla">
  <div class="pump-nozzle"></div><div class="pump-stem"></div><div class="pump-collar"></div>
  <div class="body"><div class="label">
    <div class="brand">Norvane</div>
    <div class="variant-line">Vanilla</div>
    <div class="variant-name">Dream</div>
    <div class="art" role="img" aria-label="Vanilla pods with a vanilla flower"></div>
    <div class="size-box"><span class="kind">HAND WASH</span><span class="volume">- 400 mL -</span></div>
  </div></div>
</article>

<article class="bottle rose">
  <div class="pump-nozzle"></div><div class="pump-stem"></div><div class="pump-collar"></div>
  <div class="body"><div class="label">
    <div class="brand">Norvane</div>
    <div class="variant-line accent">Rose</div>
    <div class="variant-name">Oud</div>
    <div class="art" role="img" aria-label="Pink rose with leaves"></div>
    <div class="size-box"><span class="kind">HAND WASH</span><span class="volume">- 400 mL -</span></div>
  </div></div>
</article>

<article class="bottle sandalwood">
  <div class="pump-nozzle"></div><div class="pump-stem"></div><div class="pump-collar"></div>
  <div class="body"><div class="label">
    <div class="brand">Norvane</div>
    <div class="variant-line">Oud and</div>
    <div class="variant-name long">Sandalwood</div>
    <div class="art" role="img" aria-label="Sandalwood pieces with green leaves"></div>
    <div class="size-box"><span class="kind">HAND WASH</span><span class="volume">- 400 mL -</span></div>
  </div></div>
</article>

<article class="bottle musk">
  <div class="pump-nozzle"></div><div class="pump-stem"></div><div class="pump-collar"></div>
  <div class="body"><div class="label">
    <div class="brand">Norvane</div>
    <div class="variant-name">Musk</div>
    <div class="art" role="img" aria-label="Yellow musk melon slices"></div>
    <div class="size-box"><span class="kind">HAND WASH</span><span class="volume">- 400 mL -</span></div>
  </div></div>
</article>

<article class="bottle honey">
  <div class="pump-nozzle"></div><div class="pump-stem"></div><div class="pump-collar"></div>
  <div class="body"><div class="label">
    <div class="brand">Norvane</div>
    <div class="variant-line accent">Milk and</div>
    <div class="variant-name">Honey</div>
    <div class="art" role="img" aria-label="Honey dipper with splashing honey"></div>
    <div class="size-box"><span class="kind">HAND WASH</span><span class="volume">- 400 mL -</span></div>
  </div></div>
</article>

<article class="bottle shea">
  <div class="pump-nozzle"></div><div class="pump-stem"></div><div class="pump-collar"></div>
  <div class="body"><div class="label">
    <div class="brand">Norvane</div>
    <div class="variant-line">Butter</div>
    <div class="variant-name">Shea</div>
    <div class="art" role="img" aria-label="Shea nuts with leaves"></div>
    <div class="size-box"><span class="kind">HAND WASH</span><span class="volume">- 400 mL -</span></div>
  </div></div>
</article>

<article class="bottle bloom">
  <div class="pump-nozzle"></div><div class="pump-stem"></div><div class="pump-collar"></div>
  <div class="body"><div class="label">
    <div class="brand">Norvane</div>
    <div class="variant-line accent">Velvet</div>
    <div class="variant-name">Bloom</div>
    <div class="art" role="img" aria-label="Tropical flowers and butterflies"></div>
    <div class="size-box"><span class="kind">HAND WASH</span><span class="volume">- 400 mL -</span></div>
  </div></div>
</article>

</main>
</body>
</html>
```